Wordpress Website for Trauma Ward Harm Recovery Outreach Scheme

We are looking for a wordpress website that is clean, crisp and bold for our Trauma Ward Harm Recovery Outreach Scheme.

We are a Canadian hospital in Winnipeg, MB which sees many youth injured by violence. We are starting up an Trauma Ward Harm Recovery Outreach Scheme for youth injured by violence. The youth who we will serve will be between the age of 14 - 24 and many will be gang-involved.

However, it is important to note that this website isn't for the youth themselves as much as it is for professionals and community interested in learning about our program. As such, it is should be friendly but professional. I am interested in a bold, crisp look.

I have attached our logo file for your use.
Updates

I forgot to mention that there should be a section along the bottom to include logos of funders and partners.

Also would be nice to include a spot for viewers to automatically subscribe to our newsletter by putting their email in.

I have added in a file of text that I will use - but want to easily be able to change and update (and post links etc). 

Target Market(s)

This will target a professional and community audience. We would like a crisp, bold, professional presence

Industry/Entity Type

Hospital

Requirements
Must have
• I would like a navigation bar that includes the following:

About TW-ROS (Background and Research sections)
People
Latest News
Job Opportunities
Research Opportunities
Publications & Reports
Contact TW-ROS ( a form)

I would also like a search form and a link to twitter.

While I am comfortable with Wordpress - I am not an expert. I want this to be as simple as possible for me to update.
Nice to have
• We have a great logo and only a few photos which I will upload in the next day.

We could also use stock photos for now but overtime switch these with photos of our own hospital emergency department and team. Additionally, we would like some stock photos of youth - a diverse mix but to include Aboriginal/First Nations, immigrant and caucasian youth
Should not have
• This design should not have guns, knifes, alcohol or blood/gore in there (I've learned to state this after using pixel throng for the logo! )

```html
<!DOCTYPE html>
<html lang="en">
<head>
<meta charset="utf-8">
<title>TW-ROS — Trauma Ward Harm Recovery Outreach Scheme</title>
<link href="https://fonts.googleapis.com/css2?family=Ubuntu:wght@400;500;700&display=swap" rel="stylesheet">
<style>
:root{
  --brand:#7c151b;
  --brand-dark:#560b0f;
  --ink:#222;
  --text:#555;
  --panel:#f2f2f2;
  --rule:#dcdcdc;
  --footer:#f0f0f0;
  --bar:#f7f7f7;
}
*{box-sizing:border-box;margin:0;padding:0}
html,body{width:804px;height:1200px;overflow:hidden}
body{position:relative;background:#fff;font-family:"Ubuntu",sans-serif;color:var(--text)}
a{color:inherit;text-decoration:none}
ul{list-style:none}

.brand{position:absolute;left:84px;top:38px;display:flex;align-items:center;gap:8px}
.brand-name{font-size:34px;font-weight:700;color:var(--brand);letter-spacing:-1px;line-height:1}
.brand-divider{width:1px;height:58px;background:#ccc}
.brand-tag{font-size:10.5px;line-height:12px;color:#555;width:80px}

.search{position:absolute;left:556px;top:85px;width:165px;height:18px;background:#f3f3f3;border:1px solid #ececec;font-size:6px;color:#bbb;padding:5px 6px}
.search svg{position:absolute;right:4px;top:4px}

.nav{position:absolute;left:84px;top:110px;width:636px;height:40px;background:linear-gradient(#95232a,var(--brand-dark));display:flex}
.nav a{color:#fff;font-size:10px;line-height:40px;padding:0 9px;border-right:1px solid rgba(0,0,0,.25);box-shadow:1px 0 0 rgba(255,255,255,.1)}
.nav a:first-child{padding-left:19px}
.nav a:last-child{border:none;box-shadow:none;padding:0 10px}

.hero{position:absolute;left:84px;top:154px;width:636px;height:268px;background:#000;overflow:hidden}
.hero-photo{position:absolute;right:0;top:0;width:310px;height:268px;background:linear-gradient(90deg,#000 0%,#8a0a0a 18%,#d71d1d 35%,#e8e0de 55%,#d21a1a 75%,#d9c9c6 100%)}
.hero-copy{position:absolute;left:32px;top:84px;width:285px;color:#fff}
.hero-copy h2{font-size:21px;font-weight:400;letter-spacing:.5px;margin-bottom:8px}
.hero-copy p{font-size:8.6px;line-height:16px}
.btn-more{display:inline-block;margin-top:12px;background:var(--brand);color:#fff;font-size:8.5px;padding:6px 13px}
.dots{position:absolute;left:33px;top:231px;display:flex;gap:2px}
.dots span{width:9px;height:9px;border-radius:50%;background:#444;border:1px solid #888}
.dots span:first-child{background:#fff}

.welcome{position:absolute;left:84px;top:436px;width:636px;text-align:center}
.welcome h1{font-size:16px;font-weight:400;color:var(--brand);padding-bottom:10px;border-bottom:1px solid var(--rule)}
.welcome p{font-size:8.6px;line-height:16px;margin-top:9px;text-align:justify;text-align-last:center;color:#666}

.panel{position:absolute;background:var(--panel)}
.panel-title{font-size:12px;font-weight:400;color:var(--brand);padding:14px 11px 6px;border-bottom:1px solid #e2e2e2}
.news{left:84px;top:564px;width:206px;height:226px}
.news .body{padding:10px 13px 10px 11px;font-size:8.8px;line-height:16px;color:#333;text-align:justify}
.news h4{font-size:9px;font-weight:500;color:#222;margin-bottom:4px}

.jobs{left:298px;top:564px;width:207px;height:226px}
.jobs .panel-title{padding:11px 10px 6px;border:none}
.jobs .body{padding:0 14px 0 10px;font-size:7.2px;line-height:14.6px;color:#333}
.jobs h4{font-size:8.8px;font-weight:500;color:#222;margin-bottom:6px}
.jobs h5{font-size:8.8px;font-weight:400;color:var(--brand);margin-bottom:4px}
.jobs li{position:relative;padding-left:14px;margin-bottom:4px;text-align:justify}
.jobs li::before{content:"›";position:absolute;left:2px;top:-1px;font-size:10px;color:#333}
.jobs .note{padding-left:14px;text-align:justify;width:120px}

.pubs{left:513px;top:564px;width:207px;height:398px}
.pubs-title{height:36px;background:linear-gradient(#95232a,var(--brand-dark));color:#fff;font-size:11.5px;font-weight:400;padding:11px 20px}
.pubs .body{padding:10px 22px 0 14px;font-size:8.8px;line-height:16px;color:#555}
.cite{text-align:justify}
.cite-date{margin:14px 0 8px;color:#333}
.download{display:flex;align-items:center;gap:7px;font-size:8.8px;color:#333;margin-bottom:26px}

.people{left:84px;top:798px;width:421px;height:164px}
.people .panel-title{padding:8px 13px 6px}
.photo{position:absolute;left:13px;top:37px;width:67px;height:65px;background:linear-gradient(160deg,#c98f5a,#e8c2a4 45%,#d44e7a)}
.bio{position:absolute;left:99px;top:36px;width:308px;font-size:6.9px;line-height:14.6px;color:#777;text-align:justify}
.bio .role{font-size:8.6px;color:#555;line-height:13px}
.bio .name{font-size:9px;color:#222;line-height:14px;margin-bottom:2px}

.footer{position:absolute;left:0;top:986px;width:804px;height:168px;background:var(--footer)}
.footer h3{position:absolute;top:24px;font-size:11.5px;font-weight:400;color:var(--brand)}
.footer ul{position:absolute;font-size:8.6px;line-height:16px;color:#555}
.subscribe p{position:absolute;left:432px;top:49px;width:148px;font-size:8.6px;line-height:13px;color:#777;text-align:justify}
.field{position:absolute;left:432px;width:148px;height:17px;background:#fff;border:1px solid #e4e4e4;font-size:6.5px;color:#ccc;padding:4px 6px}
.btn-sub{position:absolute;left:515px;top:136px;width:66px;height:16px;border-radius:8px;background:var(--brand);color:#fff;font-size:8.8px;text-align:center;line-height:16px}
.arrows{position:absolute;left:700px;top:26px;display:flex;gap:1px}
.partner{position:absolute;left:603px;top:64px;display:flex;align-items:center;gap:6px;font-size:13px;color:#666}
.partner i{width:16px;height:16px;border:1px solid #888;border-radius:50%}

.bottom{position:absolute;left:0;top:1154px;width:804px;height:46px;background:var(--bar);text-align:center;font-size:8.6px;color:#555;line-height:38px}
</style>
</head>
<body>

<header>
  <div class="brand">
    <span class="brand-name">TW-ROS</span>
    <span class="brand-divider"></span>
    <span class="brand-tag">Trauma Ward Harm Recovery Outreach Scheme</span>
  </div>
  <div class="search">Type search
    <svg width="9" height="9" viewBox="0 0 9 9"><circle cx="3.6" cy="3.6" r="2.6" fill="none" stroke="#999"/><line x1="5.5" y1="5.5" x2="8.3" y2="8.3" stroke="#999" stroke-width="1.2"/></svg>
  </div>
  <nav class="nav">
    <a href="#">Home</a><a href="#">About</a><a href="#">People</a><a href="#">Latest News</a><a href="#">Job Opportunities</a><a href="#">Research Opportunities</a><a href="#">Publications &amp; Reports</a><a href="#">Contact</a>
  </nav>
</header>

<section class="hero">
  <div class="hero-photo" role="img" aria-label="Portrait of a young person with the Canadian flag painted on their face"></div>
  <div class="hero-copy">
    <h2>IMMIGRANT</h2>
    <p>Lorem Ipsum is simply dummy text of the printing and typesetting industry. Lorem Ipsum has been the industry's standard dummy text ever since the 1500s, when an unknown printer took a galley of type and scrambled it to make a type specimen book.</p>
    <a class="btn-more" href="#">Read More</a>
  </div>
  <div class="dots"><span></span><span></span><span></span><span></span></div>
</section>

<section class="welcome">
  <h1>Welcome to TW-ROS</h1>
  <p>Lorem Ipsum is simply dummy text of the printing and typesetting industry. Lorem Ipsum has been the industry's standard dummy text ever since the 1500s, when an unknown printer took a galley of type and scrambled it to make a type specimen book. It has survived not only five centuries, but also the leap into electronic typesetting, remaining essentially unchanged. It was popularised in the 1960s with the release of Typeplate sheets containing Lorem Ipsum passages, and more recently with desktop publishing software like Quillset Layout including versions of Lorem Ipsum.</p>
</section>

<section class="panel news">
  <h3 class="panel-title">Latest News</h3>
  <div class="body">
    <h4>In June 2013</h4>
    <p>The youth violence research program at Prairie Institute of Youth Health, Red River University was awarded two operating grants to support the study “Coordinated Support for Youth Recovering from Injury: A Pilot Study.” These operating grants were received from the National Health Institute</p>
  </div>
</section>

<section class="panel jobs">
  <h3 class="panel-title">Job Opputunities</h3>
  <div class="body">
    <h4>Requirements of the Position</h4>
    <h5>Social Worker designation required</h5>
    <ul>
      <li>Must have experience working with youth who have experienced violence</li>
      <li>Must be willing to work both at the Red River University Fenwick Campus and in the community in providing wraparound care to youth injured by violence</li>
    </ul>
    <p class="note">Must attend Health and Safety and Privacy Act Orientation</p>
  </div>
</section>

<section class="panel pubs">
  <h3 class="pubs-title">Related Publications</h3>
  <div class="body">
    <p class="cite">Holloway ME, Varga K, Osei T, Rahimi L, Dunmore P. Community Based Participatory Research: Development of a Hospital-Based Youth Violence Intervention using Concept Mapping. Journal of Acute Care Studies</p>
    <p class="cite-date">2010 Aug;17(8):877-85. pdf</p>
    <a class="download" href="#">
      <svg width="24" height="28" viewBox="0 0 20 22"><path d="M2 1h11l5 5v15H2z" fill="#fff" stroke="#bbb"/><path d="M13 1v5h5" fill="none" stroke="#bbb"/><rect x="2" y="15" width="16" height="5" fill="#c8141c"/></svg>
      Click Here to download
    </a>
    <p class="cite">Holloway ME, Park JD. Emergency Department Dispositions among 4100 Youth Injured by Violence: A population-based study. Northern Journal of Acute Medicine;</p>
    <p class="cite-date">2007; 9(3); 164-169 pdf</p>
    <a class="download" href="#">
      <svg width="24" height="28" viewBox="0 0 20 22"><path d="M2 1h11l5 5v15H2z" fill="#fff" stroke="#bbb"/><path d="M13 1v5h5" fill="none" stroke="#bbb"/><rect x="2" y="15" width="16" height="5" fill="#c8141c"/></svg>
      Click Here to download
    </a>
  </div>
</section>

<section class="panel people">
  <h3 class="panel-title">People</h3>
  <div class="photo" role="img" aria-label="Portrait photo of the principal investigator"></div>
  <div class="bio">
    <p class="role">Principal Investigator</p>
    <p class="name">Maren Holloway</p>
    <p>Lorem Ipsum is simply dummy text of the printing and typesetting industry. Lorem Ipsum has been the industry's standard dummy text ever since the 1500s, when an unknown printer took a galley of type and scrambled it to make a type specimen book. It has survived not only five centuries, but also the leap into electronic typesetting, remaining essentially unchanged. It was popularised in the 1960s with the release of Typeplate sheets containing Lorem Ipsum passages .</p>
  </div>
</section>

<footer class="footer">
  <h3 style="left:82px">Quick Links</h3>
  <ul style="left:84px;top:51px"><li>Home</li><li>About</li><li>People</li><li>Latest News</li><li>Job Opportunities</li></ul>
  <ul style="left:192px;top:51px;line-height:17.5px"><li>Research Opportunities</li><li>Publications &amp; Reports</li><li>Contact</li></ul>
  <h3 style="left:325px">Support Links</h3>
  <ul style="left:324px;top:51px"><li>Legal Notice</li><li>Privacy Policy</li><li>Terms &amp; Conditions</li><li>Help</li></ul>
  <div class="subscribe">
    <h3 style="left:432px">Subscribe to newsletter</h3>
    <p>Sign-up for our daily emails by entering your information below:</p>
    <div class="field" style="top:83px">Name</div>
    <div class="field" style="top:111px">Enter Your E-Mail ID</div>
    <a class="btn-sub" href="#">Subscribe</a>
  </div>
  <h3 style="left:592px">Funders &amp; Partner’s</h3>
  <div class="arrows">
    <svg width="10" height="10" viewBox="0 0 10 10"><circle cx="5" cy="5" r="5" fill="#444"/><path d="M6 2.5 3.5 5 6 7.5" fill="none" stroke="#fff" stroke-width="1.3"/></svg>
    <svg width="10" height="10" viewBox="0 0 10 10"><circle cx="5" cy="5" r="5" fill="#444"/><path d="M4 2.5 6.5 5 4 7.5" fill="none" stroke="#fff" stroke-width="1.3"/></svg>
  </div>
  <div class="partner"><i></i>Harrowgate Partners</div>
</footer>

<div class="bottom">Copyright ©2013 Company Name &nbsp;- All rights reserved</div>

</body>
</html>
```